Website Design for Forklift Training Company

DO NOT CONTACT PRIVATELY. ONLY SUBMISSIONS HERE WILL BE CONSIDERED

I need a design for a website that offers forklift training courses.

The company offers accredited, onsite forklift training that are customized for the needs of each individual company. The company offers a variety of courses to operate forklifts and other machinary.

About: "KVW Training Ltd delivers bespoke onsite forklift truck operator training throught the uk.
All our instructors have a wealth of knowledge and expertise to provide your company with all your forklift truck training requirements.
KVW Training Ltd is registered and accredited by plomvex standards so you can be rest assured that all forklift training is carried out the very highest standard"

I need the following pages designed:
> a) Home Page: Include a header image, ways to contact, about snippet, overview of courses, accreditation that will be received after completing the courses. (See attachments for samples)
> b) About Page
> c) Contact Us Page
> d) Course Page Template: A page that will be used as template for the courses offered. It should contain;
1. Cover image for the course
2. A description of the course
3. A table indicating the various course options
4. Course Objectives
5. What the trainee will receive after doing the course (example: a certification)

Industrial Businesses

4 page

Colors
0054AA
0677BA
7BADD7
CADEEF
E8F1F8
0094D4
00A9DD
6FCCEA
C7EBF8
E9F6FB

• - No Search bar

```html
<!DOCTYPE html>
<html lang="en">
<head>
<meta charset="utf-8">
<title>KVW Training Ltd – Forklift Training</title>
<link href="https://fonts.googleapis.com/css2?family=Lato:wght@300;400;700;900&family=Open+Sans:wght@400&display=swap" rel="stylesheet">
<style>
:root{
  --navy:#0054AA;
  --blue:#0677BA;
  --mid:#7BADD7;
  --pale:#CADEEF;
  --mist:#E8F1F8;
  --sky:#0094D4;
  --cyan:#00A9DD;
  --aqua:#6FCCEA;
  --ice:#C7EBF8;
  --frost:#E9F6FB;
  --text:#333a44;
  --white:#ffffff;
}
*{margin:0;padding:0;box-sizing:border-box}
html,body{width:1200px;height:4284px;overflow:hidden}
body{font-family:'Lato',sans-serif;color:var(--text);background:var(--white);position:relative}

/* header */
.site-header{position:absolute;left:0;top:0;width:1200px;height:83px;background:#f4f7fb;z-index:3}
.brand{position:absolute;left:141px;top:22px;font-weight:900;font-size:27px;color:var(--cyan);letter-spacing:-.5px}
.main-nav a{position:absolute;top:28px;font-size:18px;color:#8a939c;text-decoration:none;letter-spacing:-.5px}
.main-nav a.active{color:var(--sky);font-weight:700}

/* hero */
.hero{position:absolute;left:0;top:83px;width:1200px;height:750px;overflow:hidden;background:linear-gradient(100deg,#0a3fa8 0%,#1656b8 45%,#2f6fc2 100%)}
.hero-photo{position:absolute;left:600px;top:0;width:600px;height:750px;background:linear-gradient(90deg,rgba(22,86,184,0) 0%,#6c8aa8 40%,#a9946a 75%,#8a7a5c 100%)}
.hero-wave{position:absolute;left:0;top:580px;width:1200px;height:250px}
.hero-kicker{position:absolute;left:145px;top:212px;font-size:36px;font-weight:300;color:var(--white);letter-spacing:-1px}
.hero-title{position:absolute;left:143px;top:256px;font-size:50px;font-weight:900;color:var(--white);letter-spacing:-1.5px}
.hero-text{position:absolute;left:141px;top:330px;font-size:21px;line-height:31px;color:var(--white);letter-spacing:-.6px}
.btn{position:absolute;display:flex;align-items:center;justify-content:center;width:191px;height:52px;color:var(--white);font-weight:700;font-size:16px;text-decoration:none;border-radius:0 16px 0 16px;letter-spacing:-.3px}
.btn-solid{background:var(--sky)}
.btn-grad{background:linear-gradient(90deg,var(--aqua),var(--sky) 60%,var(--navy))}

/* about */
.hex-photo{position:absolute}
.about-title{position:absolute;left:632px;top:898px;font-size:42px;font-weight:300;color:var(--navy);letter-spacing:-1.5px}
.about-title b,.section-title b{font-weight:900}
.about-copy{position:absolute;left:634px;top:972px;width:470px;font-size:19px;line-height:28px;color:#3a3f46;letter-spacing:-.5px}
.about-copy p{margin-bottom:27px}

/* courses */
.courses{position:absolute;left:0;top:1446px;width:1200px;height:1094px;background:linear-gradient(180deg,#e1f3fb 0%,#eaf6fb 100%)}
.section-title{position:absolute;left:0;width:1200px;text-align:center;font-size:40px;font-weight:300;color:var(--navy);letter-spacing:-1.5px}
.courses-sub{position:absolute;left:0;top:118px;width:1200px;text-align:center;font-style:italic;font-size:19px;color:#3a3f46;letter-spacing:-.5px}
.course-col{position:absolute;color:var(--white)}
.course-col h3{text-align:center;font-weight:900;font-size:28px;line-height:37px;letter-spacing:-1px;text-transform:uppercase}
.course-col ul{list-style:none;margin-top:14px}
.course-col li{position:relative;padding-left:30px;font-size:16.5px;height:29px;line-height:29px;letter-spacing:-.6px;white-space:nowrap}
.course-col li::before{content:"";position:absolute;left:0;top:6px;width:17px;height:17px;border-radius:50%;background:var(--white)}
.course-col li::after{content:"";position:absolute;left:5px;top:10px;width:7px;height:4px;border-left:2px solid var(--tick);border-bottom:2px solid var(--tick);transform:rotate(-45deg)}
.col-forklift{left:0;top:254px;width:389px;height:688px;background:var(--mid);padding:52px 0 0 56px;--tick:var(--mid)}
.col-forklift h3{margin-left:-56px}
.col-mewp{left:389px;top:199px;width:424px;height:796px;background:var(--navy);border-radius:36px 0 36px 0;padding:66px 0 0 46px;--tick:var(--navy);box-shadow:0 8px 20px rgba(0,40,100,.2)}
.col-mewp h3{margin-left:-46px;font-size:30px;line-height:37px}
.col-mewp li{font-size:18px;height:33px;line-height:33px}
.col-mewp li::before{top:8px;width:19px;height:19px}
.col-mewp li::after{top:13px;left:5px}
.col-other{left:813px;top:254px;width:387px;height:688px;background:var(--aqua);padding:52px 0 0 45px;--tick:var(--aqua)}
.col-other h3{margin-left:-45px}

/* accreditation */
.accreditation{position:absolute;left:0;top:2540px;width:1200px;height:850px;background:linear-gradient(180deg,#ffffff 0%,#eef7fc 100%)}
.accred-sub{position:absolute;left:0;top:130px;width:1200px;text-align:center;font-size:19px;color:#3a3f46;letter-spacing:-.4px}
.accred-card{position:absolute;top:285px;width:442px;height:449px;border:1.5px solid #7d8590;border-top:none}
.accred-card::before,.accred-card::after{content:"";position:absolute;top:0;height:1.5px;background:#7d8590;width:110px}
.accred-card::before{left:0}
.accred-card::after{right:0}
.accred-card p{position:absolute;left:28px;top:110px;width:386px;text-align:center;font-family:'Open Sans',sans-serif;font-size:15px;line-height:30.5px;color:#444b54;letter-spacing:-.4px}
.badge{position:absolute}
.badge-square{left:160px;top:-58px;width:122px;height:130px;background:var(--navy);border:3px solid #1b2a5c}
.badge-round{left:160px;top:-50px;width:122px;height:110px;border-radius:50%;background:var(--pale)}

/* contact */
.contact-title{position:absolute;left:141px;top:3497px;font-size:40px;font-weight:300;color:var(--navy);letter-spacing:-1px}
.contact-title b{font-weight:900}
.field{position:absolute;left:135px;width:425px;background:#e8eef6;border-radius:0 16px 0 16px;padding-left:22px;font-size:16px;color:#3a3f46;letter-spacing:-.3px}

/* footer */
.site-footer{position:absolute;left:0;top:4089px;width:1200px;height:195px;background:linear-gradient(180deg,#0a58b0,#0050a6)}
.footer-nav a{position:absolute;top:45px;font-size:20px;font-weight:700;color:var(--white);text-decoration:none;transform:translateX(-50%);letter-spacing:-.5px}
.copyright{position:absolute;left:0;top:96px;width:1200px;text-align:center;font-size:17px;color:var(--white);letter-spacing:-.5px}
.social{position:absolute;top:140px;width:36px;height:36px;border:2px solid var(--white);border-radius:50%}
</style>
</head>
<body>

<header class="site-header">
  <div class="brand">KVW TRAINING LTD</div>
  <nav class="main-nav">
    <a class="active" style="left:622px">ABOUT</a>
    <a style="left:774px">COURSES</a>
    <a style="left:946px">CONTACT US</a>
  </nav>
</header>

<section class="hero">
  <div class="hero-photo" role="img" aria-label="Smiling forklift operator in hard hat and hi-vis vest at the wheel in a warehouse"></div>
  <div class="hero-kicker">WELCOME TO</div>
  <h1 class="hero-title">FORKLIFT TRAINING</h1>
  <p class="hero-text">KVW Training Ltd delivers bespoke onsite<br>&nbsp;forklift &nbsp;truck operator training &nbsp;throught the uk.</p>
  <a class="btn btn-solid" style="left:141px;top:409px">LEARN MORE</a>
  <svg class="hero-wave" viewBox="0 0 1200 250" preserveAspectRatio="none">
    <path d="M0 150 C200 60 420 150 700 215 C900 255 1080 210 1200 160 L1200 250 L0 250 Z" fill="#ffffff"/>
    <path d="M0 128 C200 40 420 130 700 200 C900 240 1080 190 1200 140 L1200 150 C1080 205 900 250 700 212 C420 150 200 60 0 146 Z" fill="#ffffff" opacity=".85"/>
    <path d="M0 170 C250 110 450 170 720 228 C900 258 1080 225 1200 175 L1200 200 C1080 245 900 270 720 240 C460 190 240 140 0 190 Z" fill="#1d5fb8"/>
    <path d="M500 200 C700 240 950 250 1200 190 L1200 205 C950 262 720 252 500 208 Z" fill="#4fb2e2"/>
  </svg>
</section>

<section class="about">
  <svg class="hex-photo" style="left:96px;top:831px" width="470" height="520" viewBox="0 0 470 520">
    <defs>
      <linearGradient id="aboutPhoto" x1="0" y1="0" x2="1" y2="1">
        <stop offset="0" stop-color="#9fa4a8"/>
        <stop offset=".5" stop-color="#5d6b78"/>
        <stop offset="1" stop-color="#2e3640"/>
      </linearGradient>
    </defs>
    <polygon points="233,0 450,128 450,378 233,520 0,378 0,128" fill="url(#aboutPhoto)" role="img" aria-label="Instructor in hard hat guiding a trainee seated on a forklift"/>
    <polyline points="450,148 464,158 464,398 247,522 232,512" fill="none" stroke="#2f94d4" stroke-width="3"/>
  </svg>
  <h2 class="about-title">ABOUT <b>FORKLIFT</b></h2>
  <div class="about-copy">
    <p>KVW Training Ltd delivers bespoke onsite forklift truck operator training throught the uk.</p>
    <p>All our instructors have a wealth of knowledge and expertise to provide your company with all your forklift truck training requirements.</p>
    <p>KVW Training Ltd is registered and accredited by plomvex standards so you can be rest assured that all forklift</p>
  </div>
  <a class="btn btn-grad" style="left:628px;top:1266px">LEARN MORE</a>
</section>

<section class="courses">
  <h2 class="section-title" style="top:56px">OUR <b>COURSES</b></h2>
  <p class="courses-sub">Lorem Ipsum is simply dummy text of the printing and typesetting industry. Lorem Ipsum has been</p>

  <div class="course-col col-forklift">
    <h3>Forkit Training<br>Courses</h3>
    <ul>
      <li>Articulated Truck Training Course</li>
      <li>Multi-Way Lift Training course</li>
      <li>Counterbalance Training Course</li>
      <li>Narrow Aisle Truck Training Course</li>
      <li>Lorry Loader Training Course</li>
      <li>Llop Training Course</li>
      <li>Truck Mounted Training Course</li>
      <li>Order Picker Truck Training Course</li>
      <li>Pedestrian Training Course</li>
      <li>Pivot Steer Training Course</li>
      <li>Reach Training Course</li>
      <li>Rough Terrain Training Course</li>
      <li>Sideloader Training Course</li>
      <li>Telescopic Handeler Training Course</li>
      <li>Tow Tractor Training Course</li>
      <li>Vna Man Down Truck Training Course</li>
      <li>Vna Man Up Truck Training Course</li>
    </ul>
  </div>

  <div class="course-col col-other">
    <h3>Other Training<br>Courses</h3>
    <ul>
      <li>Skid Steer Training Course</li>
      <li>Front Loading Shovel Training Course</li>
      <li>Overhead Pendant Crane Training Course</li>
      <li>Swing Colum Jib Crane Training Course</li>
      <li>Slinging and Signalling Training Course</li>
      <li>Vehicle Banksman Training Course</li>
    </ul>
  </div>

  <div class="course-col col-mewp">
    <h3>MEWP Training<br>Courses</h3>
    <ul style="margin-top:18px">
      <li>Cherry Picker Training Course</li>
      <li>Scissor Lift Training Course</li>
      <li>Harness And Lanyard Training Course</li>
    </ul>
  </div>
</section>

<section class="accreditation">
  <h2 class="section-title" style="top:68px">FORKLIFT &nbsp;<b>ACCREDIATION</b></h2>
  <p class="accred-sub">Lorem ipsum dolor sit amet, consectetur adipiscing elit, sed do eiusmod tempor</p>

  <div class="accred-card" style="left:146px">
    <div class="badge badge-square" role="img" aria-label="Accreditation body badge"></div>
    <p>PLOMVEX is recognised throughout the united kingdom and Ireland as one of the leading material handling equipment training accrediting bodies. PLOMVEX is a founder member of the TWA (accrediting bodies association for workplace transport) and this replaced the accrediting bodies forum previously run by the NSE. They have over 40 years experience of setting training standards,accreditation and monitoring. The PLOMVEX accreditation schemes are supported by legal requirements for training.</p>
  </div>

  <div class="accred-card" style="left:615px">
    <div class="badge badge-round" role="img" aria-label="Workplace transport association badge"></div>
    <p>We are accredited by the PLOMVEX who are recognised by the national workplace safety board as competent to deliver forklift truck operator training courses. As an PLOMVEX accredited training provider we are monitored annually to ensure we are maintaining our high standards as laid down by the PLOMVEX. All our instructors are qualified and registered with the PLOMVEX and monitored. Please note we are only accredited to deliver training at customer premises as we do not have a training centre.</p>
  </div>
</section>

<section class="contact">
  <h2 class="contact-title"><b>CONTACT</b> &nbsp;US</h2>
  <div class="field" style="top:3573px;height:59px;line-height:59px">YOUR NAME*</div>
  <div class="field" style="top:3650px;height:58px;line-height:58px">E-MAIL*</div>
  <div class="field" style="top:3725px;height:58px;line-height:58px">PHONE*</div>
  <div class="field" style="top:3801px;height:128px;padding-top:18px">LEAVE MESSAGE*</div>
  <a class="btn btn-grad" style="left:141px;top:3942px">SUBMIN NOW</a>

  <svg class="hex-photo" style="left:618px;top:3479px" width="480" height="516" viewBox="0 0 480 516">
    <defs>
      <linearGradient id="contactPhoto" x1="0" y1="0" x2="1" y2="1">
        <stop offset="0" stop-color="#c9ccd0"/>
        <stop offset=".55" stop-color="#8f8f86"/>
        <stop offset="1" stop-color="#c9a43a"/>
      </linearGradient>
    </defs>
    <polygon points="250,0 476,130 476,380 250,512 26,380 26,130" fill="url(#contactPhoto)" role="img" aria-label="Instructor watching an operator drive a yellow forklift in a warehouse"/>
    <polyline points="26,148 2,162 2,392 234,512 248,504" fill="none" stroke="#2f94d4" stroke-width="3"/>
  </svg>
</section>

<footer class="site-footer">
  <nav class="footer-nav">
    <a style="left:296px">HOME</a>
    <a style="left:472px">ABOUT</a>
    <a style="left:660px">COURSES</a>
    <a style="left:873px">CONTACT US</a>
  </nav>
  <p class="copyright">Copyright 2021 Forklift Training All Right Rerserved &nbsp;Privacy Policy &nbsp;| &nbsp;Contact</p>
  <span class="social" style="left:514px"></span>
  <span class="social" style="left:559px"></span>
  <span class="social" style="left:605px"></span>
  <span class="social" style="left:650px"></span>
</footer>

</body>
</html>
```